Colin Vardek Business card

Hey there, I’m hoping to have a business card designed. I’m in Real estate and just switched to a new Brokerage called: The Harbourline Property Group

The back could just be the company name maybe or whatever looks good!

I’ve attached some logos of our company and some cards my buddy had done up.

On the card:
Colin Vardek
colinvardek@mailora.com
587-412-9065
colinvardek.ca

Target Market(s)

Home buyers and sellers

Industry/Entity Type

Real Estate

Contact Information for Business Card

just looking for a cool and modern design with my picture on it. I like the idea of Black and red being used.

Requirements
Must have
• all the details provided. I'm open to anything. Just want a professional looking card.

```html
<!DOCTYPE html>
<html lang="en">
<head>
<meta charset="utf-8">
<title>Colin Vardek – Business Card</title>
<link rel="stylesheet" href="https://fonts.googleapis.com/css2?family=Montserrat:wght@700;800&family=Lato:wght@400&display=swap">
<style>
  :root {
    --backdrop: #9a9a9a;
    --card: #000000;
    --brand-red: #d0213c;
    --ink-white: #ffffff;
    --suit-dark: #1f2733;
    --suit-mid: #2f3a4a;
  }
  * { margin: 0; padding: 0; box-sizing: border-box; }
  html, body { width: 1200px; height: 1059px; overflow: hidden; }
  body { background: var(--backdrop); position: relative; font-family: "Lato", sans-serif; }

  .card { position: absolute; background: var(--card); overflow: hidden; }
  .card--front { left: 245px; top: 82px; width: 705px; height: 404px; }
  .card--back  { left: 245px; top: 565px; width: 708px; height: 405px; }

  .brand { display: flex; align-items: flex-start; gap: 10px; z-index: 2; }
  .brand__mark { background: var(--brand-red); flex: none; }
  .brand__name {
    font-family: "Montserrat", sans-serif; font-weight: 800;
    color: var(--ink-white); text-transform: uppercase; line-height: 1.05;
    white-space: nowrap;
  }

  .card--front .brand { position: absolute; left: 44px; top: 58px; }
  .card--front .brand__mark { width: 20px; height: 20px; margin-top: 7px; }
  .card--front .brand__name { font-size: 30px; }

  .agent { position: absolute; left: 48px; top: 256px; z-index: 2; }
  .agent__name {
    font-family: "Montserrat", sans-serif; font-weight: 700;
    color: var(--brand-red); font-size: 25px; margin-bottom: 12px;
  }
  .contact { list-style: none; margin-left: -5px; }
  .contact__item {
    display: flex; align-items: center; gap: 12px;
    color: var(--ink-white); font-size: 18.5px; height: 25px;
  }
  .contact__icon { width: 19px; height: 19px; fill: var(--brand-red); flex: none; }

  .portrait {
    position: absolute; left: 458px; top: 35px; width: 247px; height: 369px; z-index: 1;
    background: radial-gradient(ellipse at 62% 65%, var(--suit-mid) 0%, var(--suit-dark) 45%, var(--card) 75%);
  }

  .card--back .brand {
    position: absolute; left: 50%; top: 50%; transform: translate(-50%, -50%);
    align-items: center; gap: 16px;
  }
  .card--back .brand__mark { width: 34px; height: 34px; }
  .card--back .brand__name { font-size: 42px; }
</style>
</head>
<body>
  <section class="card card--front" aria-label="Card front">
    <div class="brand">
      <span class="brand__mark"></span>
      <p class="brand__name">The Harbourline<br>Property Group</p>
    </div>

    <div class="agent">
      <h1 class="agent__name">Colin Vardek</h1>
      <ul class="contact">
        <li class="contact__item">
          <svg class="contact__icon" viewBox="0 0 24 24" aria-hidden="true"><path d="M6.6 10.8c1.4 2.8 3.8 5.1 6.6 6.6l2.2-2.2c.3-.3.7-.4 1-.2 1.1.4 2.3.6 3.6.6.6 0 1 .4 1 1V20c0 .6-.4 1-1 1C10.6 21 3 13.4 3 4c0-.6.4-1 1-1h3.5c.6 0 1 .4 1 1 0 1.3.2 2.5.6 3.6.1.3 0 .7-.2 1l-2.3 2.2z"/></svg>
          <span>587-412-9065</span>
        </li>
        <li class="contact__item">
          <svg class="contact__icon" viewBox="0 0 24 24" aria-hidden="true"><path d="M2 5h20v14H2z"/><path d="M2 5h20L12 12z" fill="#000"/></svg>
          <span>colinvardek@mailora.com</span>
        </li>
        <li class="contact__item">
          <svg class="contact__icon" viewBox="0 0 24 24" aria-hidden="true"><circle cx="12" cy="12" r="10"/><path d="M7 6c2 1 3 3 2 5s-3 2-3 4M14 4c0 2 2 2 3 4s-1 3 1 5M13 20c0-2 1-3 3-4" stroke="#000" stroke-width="1.6" fill="none"/></svg>
          <span>colinvardek.ca</span>
        </li>
      </ul>
    </div>

    <div class="portrait" role="img" aria-label="Portrait photo of Colin Vardek, seated in a dark suit and white shirt"></div>
  </section>

  <section class="card card--back" aria-label="Card back">
    <div class="brand">
      <span class="brand__mark"></span>
      <p class="brand__name">The Harbourline<br>Property Group</p>
    </div>
  </section>
</body>
</html>
```